Redesign of business card for Cedar Ridge Mechanical

We are looking for a new design for our business cards for Cedar Ridge Mechanical. We are a plumbing & HVAC construction company, operating on the West Coast of Canada and USA. Logo attached.
Industry/Entity Type
Construction - Plumbing & HVAC
Contact Information for Business Card
Name, address, phone numbers, email, website address
Look and feel
Each slider illustrates characteristics of the customer's brand and the style your logo design should communicate.

```html
<!DOCTYPE html>
<html lang="en">
<head>
<meta charset="utf-8">
<title>Cedar Ridge Mechanical – Business Card</title>
<link href="https://fonts.googleapis.com/css2?family=Montserrat:wght@400;500;600&display=swap" rel="stylesheet">
<style>
  :root {
    --page: #e9e4dd;
    --card-light: #ece7e0;
    --card-mid: #6f6a64;
    --card-dark: #151311;
    --gold: #d6c2a3;
    --gold-soft: #c9b596;
    --ink: #1d1b19;
  }
  * { margin: 0; padding: 0; box-sizing: border-box; }
  html, body {
    width: 1200px;
    height: 1047px;
    overflow: hidden;
    background: var(--page);
    font-family: "Montserrat", sans-serif;
  }
  .card {
    position: absolute;
    left: 100px;
    top: 251px;
    width: 1000px;
    height: 545px;
    border-radius: 24px;
    overflow: hidden;
    background: var(--card-light);
    box-shadow: 0 10px 30px rgba(0,0,0,0.12);
  }
  .wave-band {
    position: absolute;
    left: 0;
    right: 0;
    top: 150px;
    bottom: 0;
    background: linear-gradient(to bottom,
      var(--card-light) 0,
      var(--card-mid) 55px,
      var(--card-dark) 100px,
      var(--card-dark) 100%);
  }
  .brand {
    position: absolute;
    right: 36px;
    top: 60px;
    display: flex;
    align-items: center;
    gap: 22px;
  }
  .brand-square {
    width: 56px;
    height: 56px;
    background: var(--ink);
    flex: none;
  }
  .brand-name {
    font-weight: 600;
    font-size: 38px;
    line-height: 1.15;
    letter-spacing: 1px;
    color: var(--ink);
  }
  .person { position: absolute; left: 40px; top: 258px; }
  .person-name {
    font-weight: 600;
    font-size: 39px;
    letter-spacing: 1.5px;
    color: var(--gold);
  }
  .person-title {
    margin-top: 6px;
    font-weight: 400;
    font-size: 25px;
    color: var(--gold-soft);
  }
  .contact-list {
    position: absolute;
    left: 40px;
    top: 402px;
    list-style: none;
  }
  .contact-item {
    display: flex;
    align-items: center;
    gap: 10px;
    height: 38.5px;
    font-size: 25px;
    color: var(--gold-soft);
  }
  .contact-icon { width: 20px; height: 20px; flex: none; }
  .address {
    position: absolute;
    right: 34px;
    top: 438px;
    text-align: right;
    font-size: 25px;
    line-height: 38.5px;
    color: var(--gold-soft);
  }
</style>
</head>
<body>
  <div class="card">
    <div class="wave-band" role="img" aria-label="Flowing wave band in black and grey across the lower card"></div>

    <div class="brand">
      <span class="brand-square"></span>
      <span class="brand-name">CEDAR RIDGE<br>MECHANICAL</span>
    </div>

    <div class="person">
      <h1 class="person-name">DANIEL HARPER</h1>
      <p class="person-title">Managing Director</p>
    </div>

    <ul class="contact-list">
      <li class="contact-item">
        <svg class="contact-icon" viewBox="0 0 24 24"><path d="M6.6 10.8a15 15 0 0 0 6.6 6.6l2.2-2.2c.3-.3.7-.4 1-.2 1.1.4 2.3.6 3.6.6.6 0 1 .4 1 1V20c0 .6-.4 1-1 1A17 17 0 0 1 3 4c0-.6.4-1 1-1h3.5c.6 0 1 .4 1 1 0 1.3.2 2.5.6 3.6.1.3 0 .7-.2 1z" fill="var(--gold-soft)"/></svg>
        123 456 789
      </li>
      <li class="contact-item">
        <svg class="contact-icon" viewBox="0 0 24 24"><rect x="2" y="5" width="20" height="14" rx="2" fill="var(--gold-soft)"/><path d="M3 6l9 7 9-7" fill="none" stroke="var(--card-dark)" stroke-width="1.8"/></svg>
        info@yourgmail.com
      </li>
      <li class="contact-item">
        <svg class="contact-icon" viewBox="0 0 24 24"><circle cx="12" cy="12" r="10" fill="var(--gold-soft)"/><path d="M2 12h20M12 2c3 3 3 17 0 20M12 2c-3 3-3 17 0 20" fill="none" stroke="var(--card-dark)" stroke-width="1.5"/></svg>
        www.yourwebsite.com
      </li>
    </ul>

    <p class="address">Your address, City<br>State, Zip 1234</p>
  </div>
</body>
</html>
```